Business Card Design

WE are looking for a premium quality Business Cards for a Law Firm . Copies of our current business card is attached.

Contact Information for Business Card

xyz

```html
<!DOCTYPE html>
<html lang="en">
<head>
<meta charset="utf-8">
<title>Ashcombe Legal — Business Card</title>
<link rel="stylesheet" href="https://fonts.googleapis.com/css2?family=Cinzel:wght@700&family=Arimo:wght@400;700&display=swap">
<style>
  :root {
    --page: #e9e9e9;
    --card: #ffffff;
    --green: #10352a;
    --gold: #b8975a;
    --ink: #1d1d1d;
    --rule: #2a2a2a;
  }
  * { box-sizing: border-box; margin: 0; padding: 0; }
  html, body { width: 1200px; height: 1200px; overflow: hidden; background: var(--page); }
  body { position: relative; font-family: "Arimo", Arial, sans-serif; color: var(--ink); }

  .card {
    position: absolute; left: 160px; width: 880px; height: 503px;
    background: var(--card); border-radius: 26px;
  }
  .card--front { top: 67px; }
  .card--back { top: 630px; }

  .brand { position: absolute; text-align: center; color: var(--green); font-family: "Cinzel", Georgia, serif; font-weight: 700; }
  .brand__ring { display: block; margin: 0 auto; }
  .brand__name { display: block; line-height: 1; }
  .brand__sub { display: block; line-height: 1; }

  .card--front .brand { left: 560px; top: 42px; width: 260px; }
  .card--front .brand__name { font-size: 44px; margin-top: 18px; }
  .card--front .brand__sub { font-size: 20px; letter-spacing: 10px; margin-top: 8px; padding-left: 10px; }

  .holder { position: absolute; left: 60px; top: 306px; }
  .holder__name { font-family: "Cinzel", Georgia, serif; font-weight: 700; font-size: 33px; color: var(--green); letter-spacing: 1px; line-height: 1.1; }
  .holder__role { font-size: 19.5px; color: var(--gold); line-height: 25px; margin-top: 4px; }

  .office { position: absolute; right: 60px; top: 310px; text-align: right; font-size: 21px; line-height: 28px; }

  .rule { position: absolute; left: 60px; right: 60px; top: 401px; height: 1px; background: var(--rule); }

  .contact { position: absolute; top: 415px; font-size: 21px; line-height: 28px; list-style: none; }
  .contact li { display: flex; align-items: center; gap: 9px; }
  .contact--left { left: 60px; }
  .contact--right { right: 60px; }
  .contact--right li { justify-content: flex-end; }
  .contact svg { flex: none; fill: var(--green); }

  .card--back .brand { left: 290px; top: 70px; width: 300px; }
  .card--back .brand__name { font-size: 52px; margin-top: 18px; }
  .card--back .brand__sub { font-size: 23px; letter-spacing: 12px; margin-top: 8px; padding-left: 12px; }

  .branches { position: absolute; left: 40px; right: 40px; top: 337px; height: 130px; display: flex; }
  .branch { flex: 1; text-align: center; font-size: 16.5px; line-height: 21px; display: flex; flex-direction: column; justify-content: center; }
  .branch + .branch { border-left: 2px solid var(--gold); }
  .branch__city { font-weight: 700; font-size: 19px; color: var(--green); margin-bottom: 2px; }
  .branch__phone b { color: var(--green); }
</style>
</head>
<body>

<section class="card card--front">
  <div class="brand">
    <svg class="brand__ring" width="104" height="104" viewBox="0 0 104 104"><circle cx="52" cy="52" r="48" fill="none" stroke="var(--gold)" stroke-width="4"/></svg>
    <span class="brand__name">ASHCOMBE</span>
    <span class="brand__sub">LEGAL</span>
  </div>

  <div class="holder">
    <h1 class="holder__name">DANIEL ROURKE</h1>
    <p class="holder__role">Director &amp; Principal Solicitor<br>MBA, Juris Doctor</p>
  </div>

  <address class="office" style="font-style:normal">
    Level 3, Ashcombe House<br>48 Harrow Terrace<br>Kelmore, QLD 4000
  </address>

  <div class="rule"></div>

  <ul class="contact contact--left">
    <li><svg width="17" height="17" viewBox="0 0 24 24"><path d="M6.6 10.8a15.2 15.2 0 0 0 6.6 6.6l2.2-2.2c.3-.3.7-.4 1-.2 1.1.4 2.3.6 3.6.6.6 0 1 .4 1 1V20c0 .6-.4 1-1 1A17 17 0 0 1 3 4c0-.6.4-1 1-1h3.5c.6 0 1 .4 1 1 0 1.3.2 2.5.6 3.6.1.3 0 .7-.2 1z"/></svg>+61 7 3000 1482</li>
    <li><svg width="17" height="22" viewBox="0 0 14 22"><path d="M2 0h10a2 2 0 0 1 2 2v18a2 2 0 0 1-2 2H2a2 2 0 0 1-2-2V2a2 2 0 0 1 2-2zm0 3v14h10V3zm5 15.5a1 1 0 1 0 0 2 1 1 0 0 0 0-2z"/></svg>+61 0400 217 639</li>
  </ul>

  <ul class="contact contact--right">
    <li>daniel@ashcombelegal.com.au<svg width="18" height="14" viewBox="0 0 18 14"><path d="M0 0h18v14H0zm2 2v.4l7 5 7-5V2zm0 2.8V12h14V4.8l-7 5z"/></svg></li>
    <li>www.ashcombelegal.com.au<svg width="18" height="18" viewBox="0 0 18 18"><circle cx="9" cy="9" r="8"/><path d="M1 9h16M9 1c2.5 2.5 2.5 13.5 0 16M9 1c-2.5 2.5-2.5 13.5 0 16" stroke="#fff" stroke-width="1.3" fill="none"/></svg></li>
  </ul>
</section>

<section class="card card--back">
  <div class="brand">
    <svg class="brand__ring" width="120" height="120" viewBox="0 0 120 120"><circle cx="60" cy="60" r="56" fill="none" stroke="var(--gold)" stroke-width="4.5"/></svg>
    <span class="brand__name">ASHCOMBE</span>
    <span class="brand__sub">LEGAL</span>
  </div>

  <div class="branches">
    <div class="branch">
      <p class="branch__city">Melbourne</p>
      <p>Level 27, 210 Larkin Street</p>
      <p>Easton, VIC 3000</p>
      <p class="branch__phone"><b>Phone :</b> +61 03 9000 3318</p>
    </div>
    <div class="branch">
      <p class="branch__city">Sydney</p>
      <p>Level 15, Harbour Point Building</p>
      <p>72 Quarry Street</p>
      <p>Linwood, NSW 2150</p>
      <p class="branch__phone"><b>Phone :</b> +61 02 8000 4471</p>
    </div>
    <div class="branch">
      <p class="branch__city">Perth</p>
      <p>Level 28, Meridian Tower</p>
      <p>95 Calder Terrace</p>
      <p>Perth, WA 6000</p>
      <p class="branch__phone"><b>Phone :</b> +61 08 6000 2290</p>
    </div>
  </div>
</section>

</body>
</html>
```